Candle Rental Business seeks new website design

We need a new website design for a Candle hire business. The business rents out pillar candles for events such as weddings and corporate events. Our main target market is weddings. The business name is Hire a Lantern. The business name does not have a logo design.

We would like a website that is light in colours and creates a warm atmosphere. The design needs to be elegant and upmarket. There are different size candles that we hire out, ranging from 10cm diameter to 20cm diameter, flat, tall etc. All our candles are white in colour. Its just the size that differs.

We would also like to include a section for hiring out decor such as glassvases, candlebras, overlays and chairs sachets, chair covers. However, this is not the businesses main focus but an additional offering to customers.

Target Market(s)

Wedding venues and brides. Corporate events. School dances.

Industry/Entity Type

Hospitality

Logo Text

Hire a Lantern

Number of Pages Required

1 page

Font styles to use
Sans Serif
Script

Requirements
Must have
• Pictures of pillar candles. Plain white candles. The website must centre around candles.
Nice to have
• Different examples of candle centrepieces
Should not have
• Pictures must not be of brides. Pictures of surrounding is perferable.

```html
<!DOCTYPE html>
<html lang="en">
<head>
<meta charset="utf-8">
<title>Hire a Lantern — Candle Hire</title>
<link rel="stylesheet" href="https://fonts.googleapis.com/css2?family=Lato:ital,wght@0,400;0,700;1,400&family=Questrial&display=swap">
<style>
:root{
  --purple:#9a72c2;
  --purple-deep:#3a1d47;
  --pink:#c9739d;
  --pink-soft:#e79bc4;
  --ink:#1d1d1d;
  --text:#3b3b3b;
  --muted:#8a8a8a;
  --white:#ffffff;
  --footer:#2d2d2d;
  --footer-line:#474747;
  --footer-text:#d6d6d6;
}
*{margin:0;padding:0;box-sizing:border-box}
html,body{width:1200px;height:2651px;overflow:hidden;background:var(--white)}
body{position:relative;font-family:"Lato",sans-serif;color:var(--text)}
.abs{position:absolute}
.display{font-family:"Questrial",sans-serif}

/* hero */
.hero{left:0;top:0;width:1200px;height:656px;background:
  radial-gradient(ellipse at 55% 45%,#f2c27a 0%,rgba(242,194,122,0) 22%),
  radial-gradient(ellipse at 75% 35%,#d69ae8 0%,rgba(214,154,232,0) 35%),
  linear-gradient(180deg,#6b2c7c 0%,#a052b4 35%,#7a3a86 65%,#2b1530 100%)}
.topbar{left:0;top:0;width:1200px;height:100px;background:rgba(40,14,48,.55)}
.brand{left:132px;top:34px;font-size:38px;line-height:42px;color:var(--white);font-family:"Questrial",sans-serif;white-space:nowrap}
.phone{left:914px;top:18px;font-size:18px;color:var(--pink-soft);display:flex;align-items:center;gap:10px;white-space:nowrap}
.phone .dot{width:24px;height:24px;border-radius:50%;background:var(--pink);display:flex;align-items:center;justify-content:center}
.nav{top:58px;font-size:14px;color:var(--white);white-space:nowrap}
.nav.active::after{content:"";position:absolute;left:0;right:0;top:24px;height:3px;background:var(--white)}
.arrow{top:285px}
.caption{left:132px;top:600px;font-size:32px;line-height:40px;color:var(--white);letter-spacing:.5px;white-space:nowrap}
.caption-band{left:0;top:586px;width:1200px;height:70px;background:rgba(30,8,36,.45)}

/* service tiles */
.tile{top:693px;width:267px;height:134px;border-radius:4px;background:linear-gradient(180deg,#5a5a5a,#242424);box-shadow:0 14px 14px -8px rgba(0,0,0,.35);border:1px solid #555}
.tile svg{position:absolute;left:22px;top:18px}
.tile .label{position:absolute;left:112px;top:22px;font-size:21px;line-height:23px;color:#eeeeee;font-family:"Questrial",sans-serif;white-space:nowrap}
.tile .more{position:absolute;left:112px;top:78px;width:105px;height:29px;border:1px solid #e8e8e8;color:#fff;font-size:13px;font-weight:700;text-align:center;line-height:27px}

/* welcome */
.welcome-title{left:132px;top:884px;font-size:30px;line-height:36px;color:var(--ink);white-space:nowrap}
.welcome-title b{font-weight:700;font-family:"Lato",sans-serif;letter-spacing:1px}
.rule{left:132px;top:931px;width:531px;height:2px;background:#d8d8d8}
.rule-accent{left:132px;top:930px;width:108px;height:3px;background:var(--pink)}
.welcome-copy{left:132px;top:948px;width:534px;font-size:13.6px;line-height:21.7px;color:#333}
.btn-pink{left:131px;top:1085px;width:113px;height:36px;background:var(--pink);color:#fff;font-size:14px;font-weight:700;text-align:center;line-height:36px;border-radius:2px}
.video{left:739px;top:901px;width:330px;height:220px;border-radius:5px;background:linear-gradient(135deg,#8a8580,#d7d2cc 45%,#6e6862);overflow:hidden}
.video .play{position:absolute;left:142px;top:76px;width:54px;height:38px;border-radius:9px;background:#d9251d}
.video .bar{position:absolute;left:0;bottom:0;width:330px;height:34px;background:linear-gradient(180deg,#3a3a3a,#111)}

/* decor band */
.decor{left:0;top:1179px;width:1200px;height:309px;background:
  radial-gradient(circle at 12% 30%,rgba(255,255,255,.12) 0 60px,transparent 61px),
  radial-gradient(circle at 88% 70%,rgba(255,255,255,.1) 0 90px,transparent 91px),
  radial-gradient(circle at 60% 20%,rgba(255,255,255,.08) 0 70px,transparent 71px),
  linear-gradient(180deg,#a07bc6,#9169b9)}
.decor-title{left:0;width:1200px;top:1220px;text-align:center;font-size:28px;line-height:34px;color:#fff}
.decor-title b{font-weight:700;font-family:"Lato",sans-serif}
.decor-rule{left:430px;top:1267px;width:436px;height:1px;background:rgba(255,255,255,.7)}
.decor-item{top:1315px;width:200px;text-align:center;color:#fff;font-size:18px;font-weight:700;white-space:nowrap}
.decor-item .ring{width:74px;height:74px;border-radius:50%;border:3px solid #fff;margin:0 auto 18px;display:flex;align-items:center;justify-content:center}
.decor-item .ring.on{background:var(--pink-soft)}
.decor-sep{top:1316px;width:1px;height:114px;background:rgba(255,255,255,.35)}

/* testimonials */
.testi-title{left:0;width:1200px;top:1545px;text-align:center;font-size:28px;line-height:34px;color:var(--ink)}
.testi-title b{font-family:"Lato",sans-serif;font-weight:700}
.testi-rule{left:424px;top:1594px;width:392px;height:1px;background:#d6d6d6}
.testi-accent{left:536px;top:1593px;width:128px;height:3px;background:var(--pink)}
.avatar{top:1621px;width:94px;height:94px;border-radius:50%;border:4px solid var(--pink);background:linear-gradient(160deg,#c9b6a3,#7c6a5c)}
.t-name{top:1649px;font-size:14px;font-weight:700;color:#2c3d5c;white-space:nowrap}
.t-role{top:1670px;font-size:12.5px;color:var(--pink);white-space:nowrap}
.t-quote{top:1730px;width:440px;font-size:13.5px;line-height:26px;font-style:italic;color:#444;text-indent:26px}
.qmark{font-size:34px;color:#b5b5b5;font-family:Georgia,serif;line-height:1;font-style:normal}
.t-quote .qmark{left:0;top:-2px}
.testi-sep{left:599px;top:1628px;width:1px;height:200px;background:#e0e0e0}
.dot{top:1868px;width:15px;height:15px;border-radius:50%;background:#222}
.dot.hollow{background:#fff;border:2px solid #222}

/* promo */
.promo{left:0;top:1949px;width:1200px;height:375px;background:
  radial-gradient(ellipse at 24% 58%,#fff6e6 0%,#d8cbb8 10%,rgba(120,110,100,0) 30%),
  linear-gradient(90deg,#8d857d 0%,#4a4744 50%,#2d2b2a 100%)}
.promo-h{left:511px;top:2019px;font-size:26px;line-height:32px;font-weight:700;color:#fff;letter-spacing:1px;white-space:nowrap}
.promo-sub{left:511px;top:2052px;width:570px;font-size:21px;line-height:30px;color:#f1f1f1}
.promo-size{left:511px;top:2126px;font-size:18px;line-height:27px;font-weight:700;color:#fff;white-space:nowrap}
.btn-ghost{left:511px;top:2199px;width:149px;height:49px;border:1.5px solid #fff;color:#fff;font-size:18px;text-align:center;line-height:46px;border-radius:2px}

/* footer */
.footer{left:0;top:2325px;width:1200px;height:326px;background:linear-gradient(180deg,#333,#262626)}
.f-head{top:2347px;font-size:17px;color:#e6e6e6;white-space:nowrap}
.f-line{left:0;top:2386px;width:1200px;height:1px;background:var(--footer-line)}
.f-link{font-size:12.5px;color:var(--footer-text);white-space:nowrap}
.f-link::before{content:"›";color:#999;margin-right:12px}
.news{left:296px;width:250px;height:54px}
.news .date{position:absolute;left:0;top:2px;width:22px;height:28px;border:1px solid #9a9a9a;font-size:10px;font-weight:700;color:#e6e6e6;text-align:center;line-height:14px}
.news .date span{display:block;background:#777;font-size:6px;line-height:12px}
.news .t{position:absolute;left:30px;top:0;width:220px;font-size:12px;line-height:15px;font-weight:700;color:var(--purple);white-space:nowrap}
.news .d{position:absolute;left:30px;top:15px;width:220px;font-size:12px;line-height:16px;color:var(--footer-text)}
.contact{font-size:12.5px;color:var(--footer-text);line-height:20px;white-space:nowrap}
.field{left:848px;width:220px;height:30px;background:#1e1e1e;border:1px solid #4a4a4a;font-size:11px;color:#8a8a8a;padding:7px 8px}
.submit{left:848px;top:2554px;width:98px;height:30px;background:var(--purple);color:#fff;font-size:14px;font-weight:700;text-align:center;line-height:30px}
.f-bottom{left:132px;top:2600px;width:936px;height:1px;background:var(--footer-line)}
.copyright{left:132px;top:2616px;font-size:12.5px;color:var(--footer-text);white-space:nowrap}
.social{top:2614px;width:23px;height:23px;border-radius:3px;background:#f0f0f0}
.social.first{background:var(--purple)}
</style>
</head>
<body>

<!-- Hero -->
<div class="abs hero" role="img" aria-label="Reception table lit with tall glass vases and floating white pillar candles under violet light"></div>
<div class="abs topbar"></div>
<div class="abs brand">Hire a Lantern</div>
<div class="abs phone">
  <span class="dot"><svg width="12" height="12" viewBox="0 0 24 24"><path fill="#fff" d="M6.6 10.8a15 15 0 0 0 6.6 6.6l2.2-2.2c.3-.3.7-.4 1-.2 1.1.4 2.3.6 3.6.6.6 0 1 .4 1 1V20c0 .6-.4 1-1 1A17 17 0 0 1 3 4c0-.6.4-1 1-1h3.5c.6 0 1 .4 1 1 0 1.3.2 2.5.6 3.6.1.3 0 .7-.2 1z"/></svg></span>
  (555)0142-880
</div>
<div class="abs nav active" style="left:496px">Home</div>
<div class="abs nav" style="left:568px">About Us</div>
<div class="abs nav" style="left:661px">Our Products</div>
<div class="abs nav" style="left:780px">Hire Candles</div>
<div class="abs nav" style="left:896px">Décor Hire</div>
<div class="abs nav" style="left:999px">Contact Us</div>
<svg class="abs arrow" style="left:56px" width="30" height="84" viewBox="0 0 30 84"><polyline points="28,2 2,42 28,82" fill="none" stroke="#fff" stroke-width="2"/></svg>
<svg class="abs arrow" style="left:1114px" width="30" height="84" viewBox="0 0 30 84"><polyline points="2,2 28,42 2,82" fill="none" stroke="#fff" stroke-width="2"/></svg>
<div class="abs caption-band"></div>
<div class="abs caption display">Creating A Warm Atmosphere &amp; Special Touch To All Occasions</div>

<!-- Service tiles -->
<div class="abs tile" style="left:159px">
  <svg width="70" height="96" viewBox="0 0 70 96"><path d="M35 6c8 12 12 20 12 28a12 12 0 0 1-24 0c0-8 4-16 12-28z" fill="#fff"/><rect x="17" y="50" width="36" height="42" rx="3" fill="#fff"/></svg>
  <div class="label">Hire<br>Candles</div><div class="more">Read More</div>
</div>
<div class="abs tile" style="left:466px">
  <svg width="80" height="96" viewBox="0 0 80 96"><path d="M40 8c6 10 9 16 9 22a9 9 0 0 1-18 0c0-6 3-12 9-22z" fill="#fff"/><rect x="12" y="46" width="56" height="44" rx="6" fill="#fff"/></svg>
  <div class="label">Personalised<br>Candles</div><div class="more">Read More</div>
</div>
<div class="abs tile" style="left:772px">
  <svg width="80" height="96" viewBox="0 0 80 96"><rect x="8" y="40" width="18" height="44" fill="#fff"/><rect x="31" y="28" width="18" height="56" fill="#fff"/><rect x="54" y="44" width="18" height="40" fill="#fff"/><rect x="4" y="86" width="72" height="4" fill="#fff"/></svg>
  <div class="label">Décor<br>Hire</div><div class="more">Read More</div>
</div>

<!-- Welcome -->
<div class="abs welcome-title display">Welcome to <b>HIRE A LANTERN</b></div>
<div class="abs rule"></div><div class="abs rule-accent"></div>
<p class="abs welcome-copy">Lorem ipsum dolor sit amet, consectetur adipiscing elit. Nulla in sollicitudin velit, bibendum velit. Cras vel facilisis ipsum, et venenatis risus. In egestas nunc etvb eros auctor sollicitu Etiam ut enim vitae magna volutpat venenatis vitae nonprof diam. Nam nunc velit, tristique a sapien euismod, pulvinar vestibulum dui. Morbi porttitor eu erat imperdiet pretium consequat fcilelis. Cras vel facilisis ipsum, et venenatis risus. In egestas nunc etvb eros auctor sollicitu.</p>
<div class="abs btn-pink">READ MORE</div>
<div class="abs video" role="img" aria-label="Video still of white pillar candles of different heights on a table">
  <div class="play"><svg width="54" height="38" viewBox="0 0 54 38"><polygon points="21,11 35,19 21,27" fill="#fff"/></svg></div>
  <div class="bar"><svg width="330" height="34" viewBox="0 0 330 34"><polygon points="12,11 21,17 12,23" fill="#fff"/><rect x="44" y="15" width="140" height="4" rx="2" fill="#555"/><rect x="44" y="15" width="84" height="4" rx="2" fill="#d9251d"/></svg></div>
</div>

<!-- Decor hires -->
<div class="abs decor"></div>
<div class="abs decor-title display">Our Decor <b>Hires</b></div>
<div class="abs decor-rule"></div>
<div class="abs decor-item" style="left:149px"><div class="ring"><svg width="30" height="40" viewBox="0 0 30 40"><path d="M9 3h12l-2 8c5 6 6 18 4 26H7C5 29 6 17 11 11z" fill="none" stroke="#fff" stroke-width="2.5"/></svg></div>Glass Vases</div>
<div class="abs decor-sep" style="left:385px"></div>
<div class="abs decor-item" style="left:397px"><div class="ring on"><svg width="40" height="40" viewBox="0 0 40 40" fill="none" stroke="#fff" stroke-width="2.5"><path d="M6 14c0 8 6 12 14 12s14-4 14-12M20 8v30M12 38h16M6 8v6M34 8v6"/></svg></div>Candle Bars</div>
<div class="abs decor-sep" style="left:610px"></div>
<div class="abs decor-item" style="left:632px"><div class="ring"><svg width="30" height="40" viewBox="0 0 30 40" fill="none" stroke="#fff" stroke-width="2.5"><path d="M8 20V8a7 7 0 0 1 14 0v12M5 20h20v6H5zM8 26v12M22 26v12"/></svg></div>Chair Sachets</div>
<div class="abs decor-sep" style="left:845px"></div>
<div class="abs decor-item" style="left:838px"><div class="ring"><svg width="40" height="34" viewBox="0 0 40 34" fill="none" stroke="#fff" stroke-width="2.5"><path d="M8 14V8a4 4 0 0 1 4-4h16a4 4 0 0 1 4 4v6M4 14h6v8h20v-8h6v12H4zM8 26v5M32 26v5"/></svg></div>Chair Covers</div>

<!-- Testimonials -->
<div class="abs testi-title display">Client <b>Testimonials</b></div>
<div class="abs testi-rule"></div><div class="abs testi-accent"></div>
<div class="abs avatar" style="left:131px" role="img" aria-label="Portrait of a client"></div>
<div class="abs t-name" style="left:249px">Mr. Dorian Halvers</div>
<div class="abs t-role" style="left:249px">Lorem Ipsum</div>
<p class="abs t-quote" style="left:132px"><span class="qmark abs">“</span>Utm tellus dolor, dapibus eget, elemen velmki cursus eleifelta arnean auctorbni wisi et urnam. Lorem ipsum dolor sit amet, conse ctetur adipiscing elit. Nulla in sollicitudin velit, bibendum velit.Cras vel facilisis ipsum, et venenatis risus.</p>
<div class="abs qmark" style="left:536px;top:1806px">”</div>
<div class="abs testi-sep"></div>
<div class="abs avatar" style="left:635px" role="img" aria-label="Portrait of a client"></div>
<div class="abs t-name" style="left:753px">Mr. Dorian Halvers</div>
<div class="abs t-role" style="left:753px">Lorem Ipsum</div>
<p class="abs t-quote" style="left:636px"><span class="qmark abs">“</span>Utm tellus dolor, dapibus eget, elemen velmki cursus eleifelta arnean auctorbni wisi et urnam. Lorem ipsum dolor sit amet, conse ctetur adipiscing elit. Nulla in sollicitudin velit, bibendum velit.Cras vel facilisis ipsum, et venenatis risus.</p>
<div class="abs qmark" style="left:1040px;top:1806px">”</div>
<div class="abs dot" style="left:554px"></div>
<div class="abs dot hollow" style="left:579px"></div>
<div class="abs dot" style="left:604px"></div>
<div class="abs dot" style="left:630px"></div>

<!-- Promo -->
<div class="abs promo" role="img" aria-label="Close-up of a lit white pillar candle among silver festive decorations"></div>
<div class="abs promo-h">We DESIGN, MANUFACTURE &amp; PERSONALISE</div>
<div class="abs promo-sub">All Of Our CANDLES In Our Most Distinctive Handcrafted Manner!</div>
<div class="abs promo-size">Different Size Candles Ranging From<br>10cm Diameter To 20cm Diameter, Flat, Tall Etc</div>
<div class="abs btn-ghost">BUY NOW</div>

<!-- Footer -->
<div class="abs footer"></div>
<div class="abs f-head" style="left:132px">Quick Links</div>
<div class="abs f-head" style="left:306px">News / Updates</div>
<div class="abs f-head" style="left:602px">Contact Detail</div>
<div class="abs f-head" style="left:848px">Quick Contact</div>
<div class="abs f-line"></div>

<div class="abs f-link" style="left:132px;top:2401px">Home</div>
<div class="abs f-link" style="left:132px;top:2431px">About Us</div>
<div class="abs f-link" style="left:132px;top:2461px">Our Products</div>
<div class="abs f-link" style="left:132px;top:2491px">Hire Candles</div>
<div class="abs f-link" style="left:132px;top:2521px">Décor Hire</div>
<div class="abs f-link" style="left:132px;top:2551px">Contact Us</div>

<div class="abs news" style="top:2402px"><div class="date">22<span>MAR</span></div><div class="t">Duis autem vel eumsodn</div><div class="d">Lorem ipsum dolor sit ametn nk consectetuer adipiscing elit.</div></div>
<div class="abs news" style="top:2465px"><div class="date">22<span>MAR</span></div><div class="t">Duis autem vel eumsodn</div><div class="d">Lorem ipsum dolor sit ametn nk consectetuer adipiscing elit.</div></div>
<div class="abs news" style="top:2528px"><div class="date">22<span>MAR</span></div><div class="t">Duis autem vel eumsodn</div><div class="d">Lorem ipsum dolor sit ametn nk consectetuer adipiscing elit.</div></div>

<div class="abs contact" style="left:602px;top:2399px"><b>Hire A Lantern</b><br>48 Wick Lane, Emberfield<br>Street no-204518</div>
<div class="abs contact" style="left:602px;top:2479px;display:flex;gap:14px;align-items:center"><svg width="12" height="12" viewBox="0 0 24 24"><path fill="#ccc" d="M6.6 10.8a15 15 0 0 0 6.6 6.6l2.2-2.2c.3-.3.7-.4 1-.2 1.1.4 2.3.6 3.6.6.6 0 1 .4 1 1V20c0 .6-.4 1-1 1A17 17 0 0 1 3 4c0-.6.4-1 1-1h3.5c.6 0 1 .4 1 1 0 1.3.2 2.5.6 3.6.1.3 0 .7-.2 1z"/></svg>555-014-2271</div>
<div class="abs contact" style="left:602px;top:2519px;display:flex;gap:14px;align-items:center"><svg width="12" height="12" viewBox="0 0 12 12"><rect x="3" y="1" width="6" height="3" fill="#ccc"/><rect x="1" y="4" width="10" height="5" fill="#ccc"/><rect x="3" y="8" width="6" height="3" fill="#888"/></svg>555-019-3364</div>
<div class="abs contact" style="left:602px;top:2564px;display:flex;gap:14px;align-items:center"><svg width="13" height="10" viewBox="0 0 13 10"><rect x=".5" y=".5" width="12" height="9" fill="none" stroke="#ccc"/><polyline points=".5,.5 6.5,5.5 12.5,.5" fill="none" stroke="#ccc"/></svg>hello@hirealantern.com</div>

<div class="abs field" style="top:2404px">Name</div>
<div class="abs field" style="top:2440px">Email</div>
<div class="abs field" style="top:2476px;height:68px">Message</div>
<div class="abs submit">SUBMIT</div>

<div class="abs f-bottom"></div>
<div class="abs copyright">Copyright © 2016 HIRE A LANTERN | All Rights Reserved.</div>
<div class="abs social first" style="left:954px"></div>
<div class="abs social" style="left:982px"></div>
<div class="abs social" style="left:1010px"></div>
<div class="abs social" style="left:1038px"></div>

</body>
</html>
```